Vardell Switchgear - Field Service Brochure

We are looking for a one page marketing brochure that includes our rate sheet. I've attached the working we on on the rate page, several photos and several versions of our logo.

```html
<!DOCTYPE html>
<html lang="en">
<head>
<meta charset="utf-8">
<title>Vardell Switchgear – Field Service Rates</title>
<link href="https://fonts.googleapis.com/css2?family=Noto+Sans:wght@400;700&display=swap" rel="stylesheet">
<style>
  :root {
    --backdrop: #3f5a74;
    --paper: #f4f4f3;
    --slate: #5d7896;
    --slate-band: #7189a4;
    --ink: #6a7f97;
    --rule: #c9d0d8;
    --white: #ffffff;
    --sky-top: #3d6cb3;
    --sky-bottom: #7eaee0;
  }
  * { box-sizing: border-box; margin: 0; padding: 0; }
  html, body { width: 1200px; height: 1152px; overflow: hidden; }
  body {
    background: var(--backdrop);
    font-family: "Noto Sans", Verdana, sans-serif;
    position: relative;
  }
  .sheet {
    position: absolute;
    left: 200px; top: 12px;
    width: 800px; height: 1128px;
    background: var(--paper);
    overflow: hidden;
    border-bottom: 4px solid var(--slate-band);
  }
  .hero {
    position: absolute; left: 0; top: 0;
    width: 800px; height: 402px;
    background: linear-gradient(180deg, var(--sky-top) 0%, #5a8ccc 55%, var(--sky-bottom) 100%);
  }
  .brand {
    position: absolute; left: 38px; top: 38px;
    width: 340px; height: 72px;
  }
  .brand-rule { position: absolute; height: 1px; background: var(--white); }
  .brand-mark {
    position: absolute; left: 38px; top: 18px;
    width: 30px; height: 30px; background: var(--slate);
  }
  .brand-name {
    position: absolute; left: 80px; top: 12px;
    color: var(--white); font-weight: 700; font-size: 18px; letter-spacing: 0.5px;
  }
  .brand-tag {
    position: absolute; left: 96px; top: 46px;
    color: var(--white); font-weight: 700; font-size: 8px;
  }
  .band {
    position: absolute; left: 0; top: 402px;
    width: 800px; height: 111px; background: var(--slate-band);
  }
  .gallery {
    position: absolute; left: 65px; top: 362px;
    width: 658px; height: 202px;
    background: var(--white);
  }
  .photo { position: absolute; top: 7px; height: 193px; }
  .photo-left {
    left: 7px; width: 348px;
    background: linear-gradient(160deg, #2e63b8 0%, #4d86d0 60%, #8a7766 100%);
  }
  .photo-right {
    left: 363px; width: 291px;
    background: linear-gradient(165deg, #3a74c6 0%, #6ea3dc 65%, #9a8a82 100%);
  }
  .intro {
    position: absolute; left: 71px; top: 590px; width: 660px;
    color: var(--slate); font-weight: 700; font-size: 12.6px; line-height: 15.2px;
  }
  .divider {
    position: absolute; left: 71px; top: 689px;
    width: 650px; height: 1px; background: var(--rule);
  }
  .rate-col { position: absolute; top: 722px; width: 168px; }
  .rate-icon { display: block; width: 54px; height: 60px; }
  .rate-title {
    margin-top: 25px;
    color: var(--slate); font-weight: 700; font-size: 13.4px; line-height: 16px;
  }
  .rate-sub {
    color: var(--ink); font-size: 10px; line-height: 12px; min-height: 24px;
  }
  .rate-list { list-style: none; margin-top: 10px; }
  .rate-list li {
    position: relative; padding-left: 12px; margin-bottom: 6px;
    color: var(--ink); font-size: 10px; line-height: 14.7px;
  }
  .rate-list li::before {
    content: "/"; position: absolute; left: 0; top: 0; color: var(--slate);
  }
</style>
</head>
<body>
<main class="sheet">
  <div class="hero" role="img" aria-label="Photo of high-voltage switchgear insulators against a blue sky with a technician at right"></div>

  <header class="brand">
    <span class="brand-rule" style="left:0;top:26px;width:28px"></span>
    <span class="brand-rule" style="left:0;top:60px;width:28px"></span>
    <span class="brand-rule" style="left:78px;top:2px;width:262px"></span>
    <span class="brand-rule" style="left:78px;top:58px;width:262px"></span>
    <span class="brand-mark"></span>
    <span class="brand-name">VARDELL SWITCHGEAR</span>
    <span class="brand-tag">A Northline Grid Parts Inc. Company</span>
  </header>

  <div class="band"></div>

  <section class="gallery">
    <div class="photo photo-left" role="img" aria-label="Photo of two technicians in an orange lift working on substation switch equipment"></div>
    <div class="photo photo-right" role="img" aria-label="Photo of a technician on an orange lift platform beside switchgear insulators"></div>
  </section>

  <p class="intro">Vardell Switchgear Company offers an expertly trained Field Service program that can provide technical guidance and assistance for your initial installation, sustaining maintenance, and repair of equipment manufactured by Vardell Switchgear. A 4-6 week reservation for assistance is recommended to ensure that we can fully accommodate your desired schedule. Expedited service may be available upon request.</p>

  <div class="divider"></div>

  <section class="rate-col" style="left:70px">
    <svg class="rate-icon" viewBox="0 0 54 60" aria-hidden="true">
      <polygon points="27,0 54,15 54,45 27,60 0,45 0,15" fill="#6d84a0"/>
      <ellipse cx="27" cy="24" rx="14" ry="4" fill="#fff"/>
      <rect x="13" y="28" width="28" height="4" rx="2" fill="#fff"/>
      <rect x="13" y="34" width="28" height="4" rx="2" fill="#fff"/>
    </svg>
    <h2 class="rate-title">Standard Rates</h2>
    <p class="rate-sub">(on-site) up to 10 hours + travel and per diem expenses</p>
    <ul class="rate-list">
      <li>$250 x 1.00 = Monday through Friday rate per hour ($2500 minimum)</li>
      <li>$250 x 1.50 = Saturday rate per hour</li>
      <li>$250 X 2.00 = Sunday rate per hour</li>
    </ul>
  </section>

  <section class="rate-col" style="left:241px">
    <svg class="rate-icon" viewBox="0 0 54 60" aria-hidden="true">
      <polygon points="27,0 54,15 54,45 27,60 0,45 0,15" fill="#6d84a0"/>
      <ellipse cx="27" cy="24" rx="14" ry="4" fill="#fff"/>
      <rect x="13" y="28" width="28" height="4" rx="2" fill="#fff"/>
      <rect x="13" y="34" width="28" height="4" rx="2" fill="#fff"/>
    </svg>
    <h2 class="rate-title">Premium Rates</h2>
    <p class="rate-sub">(on-site) over 8 hours + travel and per diem expenses</p>
    <ul class="rate-list">
      <li>$250 X 1.50 = Over Time (9-12 hours) rate per hour</li>
      <li>$250 x 2.00 = Double Time (Over 12 hours) rate per hour</li>
      <li>$250 X 2.50 = Non-standard overnight hours</li>
    </ul>
  </section>

  <section class="rate-col" style="left:420px">
    <svg class="rate-icon" viewBox="0 0 54 60" aria-hidden="true">
      <polygon points="27,0 54,15 54,45 27,60 0,45 0,15" fill="#6d84a0"/>
      <ellipse cx="27" cy="24" rx="14" ry="4" fill="#fff"/>
      <rect x="13" y="28" width="28" height="4" rx="2" fill="#fff"/>
      <rect x="13" y="34" width="28" height="4" rx="2" fill="#fff"/>
    </svg>
    <h2 class="rate-title">Expenses</h2>
    <p class="rate-sub">(on-site) up to 10 hours + travel and per diem expenses</p>
    <ul class="rate-list">
      <li>Airfare - invoiced at actual cost + 25%</li>
      <li>Lodging - invoiced at actual cost + 25%</li>
      <li>Meals and Incidentals – invoiced at cost (not to exceed $100/day)</li>
      <li>Rental Vehicle and related costs – Invoiced at cost +25%</li>
    </ul>
  </section>

  <section class="rate-col" style="left:596px;width:170px">
    <svg class="rate-icon" viewBox="0 0 54 60" aria-hidden="true">
      <polygon points="27,0 54,15 54,45 27,60 0,45 0,15" fill="#6d84a0"/>
      <ellipse cx="27" cy="28" rx="14" ry="4" fill="#fff"/>
      <rect x="13" y="32" width="28" height="4" rx="2" fill="#fff"/>
    </svg>
    <h2 class="rate-title">Minimum Charge</h2>
    <p class="rate-sub"></p>
    <ul class="rate-list">
      <li>The minimum charge, excluding travel time and expenses shall be the equivalent of one 10 hour day</li>
      <li>Cancellation charge of 4 standard hours plus any non-cancellable airfare or lodging charges shall apply</li>
      <li>Employee Drug Screening</li>
      <li>Drug screening and/or background check costs (if required by customer) shall be invoiced at actual cost plus 30%.</li>
    </ul>
  </section>
</main>
</body>
</html>
```